Corporate brochure design 4 pages

Hi,

We are a real estate company based in Europe.

We have almost finalized a rebranding.

We are developing a brand book guidelines (still on working process) to help you undertstand the look and feel of our new CI. I would like to receive proposals of design for a corporate brochure template. I need to receive the Indesign files with full ownership rights to be able to adapt all our documentation with this template.
Regarding the images, you can take gabaris on www.pelvarimages.example. I will be able to take them afterwards.

There will be 4 pages. you will receive the 4 pages on pdf for your consideration with our (almost) actual layout.

- 1st page: cover
- 2nd page: company presentation in french and english
- 3rd page: some market data + graph
- 4th page: 2 retail centers presentation.

In the template, i need to have:
- the paragraph styles in order
- 2 different masters with top/bottom/page number aso.

Please feel free to ask any other questions.

best regards,
Updates

I would like to precise tha t we are active on the commercial real estate sector:

- office transactions (rent /sales)
- property management of administrative and business buildings
- Valuation of properties
- Capital markets (investment advices for selling building)

Industry/Entity Type

Real Estate

Colors

Designer to choose colors to be used in the design.

```html
<!DOCTYPE html>
<html lang="en">
<head>
<meta charset="utf-8">
<title>Corporate Brochure – Inner Spread</title>
<link href="https://fonts.googleapis.com/css2?family=Russo+One&family=Open+Sans:wght@400;600;700&display=swap" rel="stylesheet">
<style>
  :root{
    --orange:#e07b2e;
    --ink:#2b2b2b;
    --text:#3a3a3a;
    --paper:#ffffff;
    --backdrop:#e9e9e9;
    --chart-dark:#3b3b3b;
    --chart-mid:#6d6d6d;
    --marker-blue:#7c93c4;
  }
  *{box-sizing:border-box;margin:0;padding:0}
  html,body{width:1200px;height:800px;overflow:hidden;background:var(--backdrop)}
  body{font-family:"Open Sans",Arial,sans-serif;color:var(--text)}
  .spread{position:absolute;left:60px;top:18px;width:1080px;height:764px;display:flex;box-shadow:0 6px 24px rgba(0,0,0,.15)}
  .page{position:relative;width:540px;height:764px;background:var(--paper);overflow:hidden}
  .page--left{box-shadow:inset -14px 0 18px -14px rgba(0,0,0,.18)}
  .page--right{box-shadow:inset 14px 0 18px -14px rgba(0,0,0,.18)}
  .photo{position:absolute}
  .heading{font-family:"Russo One",Arial,sans-serif;font-size:28px;line-height:1;color:var(--ink);text-transform:uppercase;font-weight:400;white-space:nowrap}
  .heading .accent{color:var(--orange)}
  .subhead{font-weight:700;color:var(--orange);font-size:11.5px;line-height:1.3}
  .body-copy{font-size:12px;line-height:1.45;color:var(--text)}
  .body-copy + .body-copy{margin-top:12px}
  .block{position:absolute}
  .align-right{text-align:right}
  /* left page */
  .photo--agent{left:0;top:0;width:220px;height:235px;background:linear-gradient(180deg,#6fa3d9 0%,#9cc0e0 40%,#5d8a3e 72%,#2f3a4a 100%)}
  .block--what{left:245px;top:28px;width:270px}
  .block--who{left:26px;top:262px;width:210px}
  .block--who .heading{font-size:26px}
  .photo--client{left:248px;top:392px;width:270px;height:200px;background:linear-gradient(135deg,#f2f2f2 0%,#d9d9d9 50%,#a9a39c 100%)}
  .block--client-text{left:248px;top:608px;width:270px}
  /* right page */
  .block--services{left:30px;top:28px;width:250px}
  .service{position:relative;padding-left:14px;margin-top:14px}
  .service::before{content:"";position:absolute;left:0;top:2px;width:5px;height:13px;background:var(--orange)}
  .service .subhead{text-transform:uppercase;margin-bottom:4px}
  .quote-band{position:absolute;left:300px;top:0;width:240px;height:92px;background:var(--orange);color:#fff;font-weight:700;font-style:italic;font-size:13.5px;line-height:1.35;padding:16px 22px}
  .photo--building{left:300px;top:92px;width:240px;height:218px;background:linear-gradient(180deg,#bcd3ea 0%,#8fb0cf 45%,#7c8a97 70%,#c9c9c9 100%)}
  .block--growth{left:296px;top:330px;width:226px}
  .block--growth .heading{font-size:22px}
  .growth-list{list-style:none;margin-top:14px}
  .growth-list li{position:relative;font-size:11px;text-transform:uppercase;line-height:1.5;padding-right:16px;color:var(--text)}
  .growth-list li::after{content:"";position:absolute;right:0;top:4px;width:8px;height:8px;background:var(--marker-blue)}
  .chart{position:absolute;left:70px;top:520px;width:180px;text-align:center}
  .chart-caption{font-size:11px;margin-top:6px}
  .chart-label{font-size:10px;fill:#fff;font-family:"Open Sans",Arial,sans-serif}
</style>
</head>
<body>
<main class="spread">
  <section class="page page--left">
    <div class="photo photo--agent" role="img" aria-label="Business agent holding a folder in front of a suburban house"></div>

    <div class="block block--what align-right">
      <h2 class="heading"><span class="accent">What</span> we do?</h2>
      <p class="subhead" style="margin-top:8px">Ut enim ad minim veniam, quis nostrud in exercitation ullamco laboris nisi ut aliquip</p>
      <p class="body-copy" style="margin-top:10px">Lorem ipsum dolor sit amet, consectetur adipisicing elit, sed do eiusmod tempor incididunt ut labore et dolore magna.</p>
      <p class="subhead" style="margin-top:10px">Duis aute irure dolor in reprehenderit in voluptate velit esse cillum dolore eu fugiat nulla pariatur</p>
    </div>

    <div class="block block--what-more" style="position:absolute;left:245px;top:262px;width:270px">
      <p class="body-copy">Excepteur sint occaecat cupidatat non proident, sunt in culpa qui officia deserunt mollit anim. Ut enim ad minim veniam, quis nostrud laborum.</p>
    </div>

    <div class="block block--who">
      <h2 class="heading"><span class="accent">Who</span> we are?</h2>
      <p class="subhead" style="margin-top:6px">Lorem ipsum dolor sit amet</p>
      <p class="body-copy" style="margin-top:10px">Lorem ipsum dolor sit amet etus adipisicing elit, sed do eiusmod tempor incididunt ut labore et dolore magna aliqua.</p>
      <p class="body-copy">Ut enim ad minim veniam, quisis nostrud isos exercitation ulamco laboris nisis ut aliquip ex eanodo quatn Duis aute irure dolor in henderin in voluptate velit essen cillum iris dolore eu fugiat nulla pariatur. Is Excepteur sint caecat cupidatat non proident, sunt in quin officia deserunt mollit inim id isi est laborum.</p>
      <p class="body-copy">laboris nisis ut aliquip ex eanodo quatn Duis aute irure dolor insim henderin.</p>
    </div>

    <div class="photo photo--client" role="img" aria-label="Smiling client holding a small model house"></div>
    <div class="block block--client-text">
      <p class="body-copy">Ut enim ad minim veniam, quisis nostrud sos exercitation nlamco laboris nisis utquip ex eanodo quatn Duis aute irure dolorinsin srin in voluptate velit essen</p>
    </div>
  </section>

  <section class="page page--right">
    <div class="block block--services">
      <h2 class="heading"><span class="accent">Our</span> services</h2>
      <p class="subhead" style="margin-top:6px">Ut enim ad minim veniam, quis nostrud</p>
      <div class="service">
        <p class="subhead">Ut enim ad minim veniam, quis idn</p>
        <p class="body-copy">Lorem ipsum dolor sit amet, onsectetur adipisicing elit, sed do eiusmod tempor incididunt ut labore et dolore magna in aliqua. Ut enim ad minim veniam, quis nostrud exercitation ullamco laboris ut aliquip ex ea commodo consequat.</p>
      </div>
      <div class="service">
        <p class="subhead">Ut enim ad minim veniam, quis idn</p>
        <p class="body-copy">Lorem ipsum dolor sit amet, onsectetur adipisicing elit, sed do eiusmod tempor incididunt ut labore et dolore magna in aliqua. Ut enim ad minim veniam, quis nostrud exercitation ullamco laboris ut aliquip ex ea commodo consequat.</p>
      </div>
      <div class="service">
        <p class="subhead">Ut enim ad minim veniam, quis idn</p>
        <p class="body-copy">Lorem ipsum dolor sit amet, onsectetur adipisicing elit, sed do eiusmod tempor incididunt ut labore et dolore magna in aliqua.</p>
      </div>
    </div>

    <blockquote class="quote-band">“Sed ut perspiciatis unde omnis iste natus error sit voluptatem accusantium”</blockquote>
    <div class="photo photo--building" role="img" aria-label="Modern glass office building with trees"></div>

    <figure class="chart">
      <svg width="140" height="140" viewBox="0 0 140 140" aria-label="Donut chart: 60%, 30%, 20%">
        <g transform="rotate(-90 70 70)" fill="none" stroke-width="26">
          <circle cx="70" cy="70" r="52" stroke="var(--orange)" stroke-dasharray="178.2 326.7"/>
          <circle cx="70" cy="70" r="52" stroke="var(--chart-mid)" stroke-dasharray="89.1 326.7" stroke-dashoffset="-178.2"/>
          <circle cx="70" cy="70" r="52" stroke="var(--chart-dark)" stroke-dasharray="59.4 326.7" stroke-dashoffset="-267.3"/>
        </g>
        <text class="chart-label" x="119" y="89" text-anchor="middle">60%</text>
        <text class="chart-label" x="19" y="77" text-anchor="middle">30%</text>
        <text class="chart-label" x="54" y="25" text-anchor="middle">20%</text>
      </svg>
      <figcaption class="chart-caption">laboris nisis ut aliquip</figcaption>
    </figure>

    <div class="block block--growth align-right">
      <h2 class="heading"><span class="accent">Company</span> grouth</h2>
      <p class="subhead" style="margin-top:6px;text-transform:uppercase">Ut enim ad minim veniam, quis idn</p>
      <p class="body-copy" style="margin-top:8px">Lorem ipsum dolor sit amet, onsectetur adipisicing elit, sed do eiusmod tempor incididunt ut labore et dolore magna in aliqua.</p>
      <ul class="growth-list">
        <li>Ut enim ad minim venam quiss</li>
        <li>Iud exercitation ullamco sirs</li>
        <li>Issi ut aliquip ex ea idosequat.</li>
      </ul>
    </div>
  </section>
</main>
</body>
</html>
```